need corporate, modern business card created for Consulting Company

I need a slick business card using elements from my website, as well as, integrating my pixelforge-created logo (see files).

The business card needs to be:
1. Corporate and modern
2. Clean and professional

I've included a PSD with the logo/icon that you can use to create it. Feel free to try a metallic finish on the logo, make it bigger/small, underlay it. Whatever you need to do to make my card stand out.

Try a black background, or white background or gray.

The idea is for my card to be memorable as well as professional and corporate.

Target Market(s)

Corporate business in the US and Canada.

Industry/Entity Type

Business

Contact Information for Business Card

Commerce Advancing Methods
Martin Coles, Senior Partner
office: 1 877 555 0143
mobile: 1 519 555 0172
website: http://www.brightvale.example

Requirements
Must have
• Card-related information
• corporate, yet modern
• clean and professional
• incorporate the icon only
• must have an editable form when complete!
Nice to have
• metallic icon might be cool
• try it with white or black

```html
<!DOCTYPE html>
<html lang="en">
<head>
<meta charset="utf-8">
<title>Brightvale Business Card</title>
<link rel="stylesheet" href="https://fonts.googleapis.com/css2?family=Tinos:wght@400;700&display=swap">
<style>
  :root {
    --page-bg: #e6e7e9;
    --card-black: #252526;
    --card-blue: #3069bf;
    --band-grey: #a8aaae;
    --text-light: #ffffff;
    --brand-blue: #3a73cc;
  }
  html, body {
    margin: 0;
    padding: 0;
    width: 1200px;
    height: 901px;
    overflow: hidden;
    background: var(--page-bg);
  }
  .stage {
    position: relative;
    width: 1200px;
    height: 901px;
  }
  .business-card {
    position: absolute;
    left: 75px;
    top: 150px;
    width: 1050px;
    height: 600px;
    filter: drop-shadow(0 10px 24px rgba(0,0,0,0.22));
  }
  .card-text {
    font-family: "Tinos", "Times New Roman", serif;
    fill: var(--text-light);
  }
  .brand-name {
    font-family: "Tinos", "Times New Roman", serif;
    font-weight: 700;
    font-size: 104px;
    fill: var(--brand-blue);
  }
  .contact-line { font-size: 21px; }
  .person-name { font-size: 30px; }
  .person-role { font-size: 25px; }
</style>
</head>
<body>
<main class="stage">
  <svg class="business-card" viewBox="0 0 1050 600" xmlns="http://www.w3.org/2000/svg" role="group" aria-label="Brightvale business card front">
    <defs>
      <clipPath id="card-shape">
        <rect x="0" y="0" width="1050" height="600" rx="70" ry="70"/>
      </clipPath>
    </defs>
    <g clip-path="url(#card-shape)">
      <rect class="base-blue" x="0" y="0" width="1050" height="600" fill="var(--card-blue)"/>
      <path class="thin-grey-line" d="M0,0 L152,0 C302,292 622,444 1050,484 L1050,0 Z" fill="var(--band-grey)"/>
      <path class="thin-blue-gap" d="M0,0 L146,0 C296,286 616,436 1050,476 L1050,0 Z" fill="var(--card-blue)"/>
      <path class="grey-band" d="M0,0 L136,0 C286,276 606,424 1050,464 L1050,0 Z" fill="var(--band-grey)"/>
      <path class="blue-edge" d="M0,0 L120,0 C270,256 592,400 1050,440 L1050,0 Z" fill="var(--card-blue)"/>
      <path class="black-field" d="M0,0 L112,0 C262,248 586,392 1050,432 L1050,0 Z" fill="var(--card-black)"/>
    </g>

    <g class="brand-lockup">
      <rect class="brand-square" x="470" y="142" width="48" height="48" fill="var(--brand-blue)"/>
      <text class="brand-name" x="540" y="196">brightvale</text>
    </g>

    <g class="contact-block">
      <g class="contact-item">
        <circle cx="62" cy="356" r="9" fill="var(--text-light)"/>
        <path d="M62,350 a4,4 0 1 1 -0.1,0 Z M62,360 l-3,-4 h6 Z" fill="var(--card-blue)"/>
        <text class="card-text contact-line" x="82" y="363">Suite # 410, Elm Bldg,</text>
        <text class="card-text contact-line" x="82" y="386">NY 10452</text>
      </g>
      <g class="contact-item">
        <circle cx="62" cy="413" r="9" fill="var(--text-light)"/>
        <rect x="58" y="409" width="8" height="8" fill="var(--card-blue)"/>
        <text class="card-text contact-line" x="82" y="420">1 877 555 0143</text>
      </g>
      <g class="contact-item">
        <circle cx="62" cy="436" r="9" fill="var(--text-light)"/>
        <rect x="59" y="431" width="6" height="10" rx="1.5" fill="var(--card-blue)"/>
        <text class="card-text contact-line" x="82" y="443">1 519 555 0172</text>
      </g>
      <g class="contact-item">
        <circle cx="62" cy="474" r="9" fill="var(--text-light)"/>
        <circle cx="62" cy="474" r="4.5" fill="none" stroke="var(--card-blue)" stroke-width="2"/>
        <text class="card-text contact-line" x="82" y="481">name@brightvale.example</text>
        <text class="card-text contact-line" x="82" y="504">www.brightvale.example</text>
      </g>
    </g>

    <g class="person-block">
      <text class="card-text person-name" x="1000" y="522" text-anchor="end">Martin Coles</text>
      <text class="card-text person-role" x="1000" y="556" text-anchor="end">Senior Partner</text>
    </g>
  </svg>
</main>
</body>
</html>
```